Business card for event manager / organizer "waiter service"

Draft of a new valuable business card for my company.
Events, personnel service providers, festivals

```html
<!DOCTYPE html>
<html lang="de">
<head>
<meta charset="utf-8">
<title>Jannik´s Kellnerservice – Visitenkarte</title>
<link rel="stylesheet" href="https://fonts.googleapis.com/css2?family=Poppins:wght@300;400;600;800&display=swap">
<style>
  :root{
    --stage:#3a3a3c;
    --card:#141414;
    --orange:#f08322;
    --white:#ffffff;
    --muted:#d9d9d9;
  }
  *{box-sizing:border-box;margin:0;padding:0}
  html,body{width:1200px;height:900px;overflow:hidden}
  body{
    background:var(--stage);
    font-family:"Poppins",sans-serif;
    color:var(--white);
    display:flex;flex-direction:column;align-items:center;justify-content:center;gap:34px;
  }
  .card{
    width:700px;height:400px;border-radius:22px;
    background:var(--card);
    position:relative;overflow:hidden;
    box-shadow:0 10px 24px rgba(0,0,0,.45);
  }
  .card--front{display:flex;align-items:center;justify-content:center}
  .brand{display:flex;align-items:center;gap:22px}
  .brand__mark{width:92px;height:92px;background:var(--orange);flex:none}
  .brand__name{font-weight:800;font-size:44px;line-height:1.02;text-transform:uppercase;color:var(--white);letter-spacing:.5px}
  .brand__tagline{font-weight:300;font-size:19px;color:var(--muted);margin-top:10px;white-space:nowrap}
  .card--back{
    background:radial-gradient(ellipse 300px 320px at 78% 30%, #5a5a5a 0%, #2a2a2a 45%, var(--card) 80%);
  }
  .portrait{
    position:absolute;right:40px;top:26px;width:230px;height:374px;
    background:linear-gradient(180deg,#2b2b2e 0%,#111114 60%,#0b0b0d 100%);
    border-radius:110px 110px 0 0;
  }
  .back__content{position:absolute;left:40px;top:32px}
  .brand--small{gap:12px}
  .brand--small .brand__mark{width:44px;height:44px}
  .brand--small .brand__name{font-size:21px}
  .brand--small .brand__tagline{font-size:10px;margin-top:4px}
  .person{margin-top:38px}
  .person__name{font-weight:600;font-size:34px;color:var(--orange);line-height:1.1}
  .person__role{font-weight:300;font-size:18px;color:var(--white);margin:4px 0 0 18px}
  .contact{list-style:none;margin:16px 0 0 18px}
  .contact li{display:flex;align-items:center;gap:12px;font-size:17px;font-weight:400;line-height:1.5;white-space:nowrap}
  .contact svg{width:17px;height:17px;flex:none;fill:var(--orange)}
  .contact .dot{width:15px;height:15px;background:var(--orange);border-radius:3px;flex:none;margin-left:1px}
</style>
</head>
<body>
  <section class="card card--front">
    <div class="brand">
      <div class="brand__mark"></div>
      <div>
        <div class="brand__name">Jannik´s<br>Kellnerservice</div>
        <div class="brand__tagline">…weil jedes Fest guten Service verdient!</div>
      </div>
    </div>
  </section>

  <section class="card card--back">
    <div class="portrait" role="img" aria-label="Porträtfoto des Inhabers in schwarzem Hemd vor grauem Studiohintergrund"></div>
    <div class="back__content">
      <div class="brand brand--small">
        <div class="brand__mark"></div>
        <div>
          <div class="brand__name">Jannik´s<br>Kellnerservice</div>
          <div class="brand__tagline">…weil jedes Fest guten Service verdient!</div>
        </div>
      </div>
      <div class="person">
        <div class="person__name">Jannik Vollmer</div>
        <div class="person__role">Inhaber</div>
      </div>
      <ul class="contact">
        <li><svg viewBox="0 0 24 24"><path d="M6.6 10.8a15 15 0 0 0 6.6 6.6l2.2-2.2a1 1 0 0 1 1-.25 11.4 11.4 0 0 0 3.6.57 1 1 0 0 1 1 1V20a1 1 0 0 1-1 1A17 17 0 0 1 3 4a1 1 0 0 1 1-1h3.5a1 1 0 0 1 1 1c0 1.25.2 2.45.57 3.57a1 1 0 0 1-.25 1z"/></svg>02361 555 01 23</li>
        <li><svg viewBox="0 0 24 24"><path d="M6.6 10.8a15 15 0 0 0 6.6 6.6l2.2-2.2a1 1 0 0 1 1-.25 11.4 11.4 0 0 0 3.6.57 1 1 0 0 1 1 1V20a1 1 0 0 1-1 1A17 17 0 0 1 3 4a1 1 0 0 1 1-1h3.5a1 1 0 0 1 1 1c0 1.25.2 2.45.57 3.57a1 1 0 0 1-.25 1z"/></svg>0170 555 48 27</li>
        <li><svg viewBox="0 0 24 24"><path d="M12 2a10 10 0 1 0 0 20 10 10 0 0 0 0-20zm0 2c.9 0 2.2 1.8 2.8 5H9.2C9.8 5.8 11.1 4 12 4zM4.3 9h2.9a20 20 0 0 0 0 6H4.3a8 8 0 0 1 0-6zm4.9 0h5.6a18 18 0 0 1 0 6H9.2a18 18 0 0 1 0-6zm7.6 0h2.9a8 8 0 0 1 0 6h-2.9a20 20 0 0 0 0-6zM9.2 17h5.6c-.6 3.2-1.9 5-2.8 5s-2.2-1.8-2.8-5z"/></svg>www.janniks-kellnerservice.de</li>
        <li><svg viewBox="0 0 24 24"><path d="M2 5h20v14H2zm2 2v.4l8 5.1 8-5.1V7z"/></svg>info@janniks-kellnerservice.de</li>
        <li><svg viewBox="0 0 24 24"><path d="M12 2a7 7 0 0 0-7 7c0 5 7 13 7 13s7-8 7-13a7 7 0 0 0-7-7zm0 9.5A2.5 2.5 0 1 1 12 6.5a2.5 2.5 0 0 1 0 5z"/></svg>Lindenweg 14, 45700 Musterstadt</li>
        <li><span class="dot"></span>@janniks-kellnerservice</li>
      </ul>
    </div>
  </section>
</body>
</html>
```